We need a business card design for a new company located in Larkmoor, LK, entitled 'BrightPath Chiropractic & Holistic Center'. Our services include restoration of health and vitality, spinal exam, health assessment, dietary & fitness programs, lymphatic & therapeutic massage, detox & remineralize body wraps, far infrared sauna therapy

Industry/Entity Type

Business

Contact Information for Business Card

BrightPath Chiropractic & Holistic Center, Marlene Okafor LMT, 4215 Elm Ridge Rd., Suite 310, Larkmoor, LK 77482, 555-214-0193

```html
<!DOCTYPE html>
<html lang="en">
<head>
<meta charset="utf-8">
<title>BrightPath Chiropractic &amp; Holistic Center – Business Card</title>
<link rel="stylesheet" href="https://fonts.googleapis.com/css2?family=Cinzel:wght@400&family=Open+Sans:wght@400;700&display=swap">
<style>
  :root {
    --backdrop: #d8ccb6;
    --card-black: #050505;
    --band-light: #eef2d6;
    --band-mid: #d9e7a6;
    --accent-pink: #d66fb4;
    --name-green: #c9e25c;
    --heading-green: #c3dc55;
    --text-white: #f2f2f2;
    --text-grey: #bdbdbd;
    --emblem-fill: #eef0d4;
  }
  * { box-sizing: border-box; margin: 0; padding: 0; }
  html, body { width: 1200px; height: 780px; overflow: hidden; }
  body { background: var(--backdrop); position: relative; font-family: "Open Sans", sans-serif; }

  .card {
    position: absolute;
    width: 540px;
    height: 310px;
    background: var(--card-black);
    overflow: hidden;
    box-shadow: 0 10px 24px rgba(0,0,0,.35);
  }
  .card--front { left: 40px; top: 60px; }
  .card--back { left: 620px; top: 410px; }

  .band {
    position: absolute;
    left: 0; right: 0;
    top: 42px;
    height: 98px;
    background: linear-gradient(90deg, var(--band-light) 0%, var(--band-mid) 45%, var(--band-light) 100%);
  }
  .band-rule {
    position: absolute;
    left: 0; right: 0;
    height: 3px;
    background: var(--accent-pink);
  }
  .band-rule--top { top: 33px; }
  .band-rule--bottom { top: 146px; }

  .emblem {
    position: absolute;
    top: 82px;
    width: 124px;
    height: 124px;
    border-radius: 50%;
    background: radial-gradient(circle, #e6efbf 0%, var(--emblem-fill) 70%);
    border: 4px solid var(--card-black);
    box-shadow: 0 0 0 3px var(--emblem-fill), 0 0 0 6px var(--card-black);
    display: flex;
    align-items: center;
    justify-content: center;
  }
  .card--front .emblem { left: 60px; }
  .card--back .emblem { left: 360px; }
  .emblem-name {
    font-family: "Cinzel", serif;
    font-weight: 400;
    font-size: 15px;
    color: var(--accent-pink);
  }

  .identity {
    position: absolute;
    left: 208px;
    top: 156px;
    right: 14px;
  }
  .company-name {
    font-family: "Cinzel", serif;
    font-weight: 400;
    font-size: 19px;
    line-height: 23px;
    color: var(--accent-pink);
    text-transform: uppercase;
  }
  .person-name {
    margin-top: 4px;
    font-weight: 700;
    font-size: 21px;
    color: var(--name-green);
  }
  .contact-line {
    font-size: 12px;
    line-height: 18px;
    color: var(--text-white);
    white-space: nowrap;
  }
  .contact-line--phone { margin-top: 4px; }

  .services-heading {
    position: absolute;
    left: 200px;
    top: 178px;
    font-weight: 700;
    font-size: 16px;
    letter-spacing: .5px;
    color: var(--heading-green);
    text-transform: uppercase;
  }
  .services-list {
    position: absolute;
    left: 30px;
    top: 214px;
    list-style: none;
    font-size: 13px;
    line-height: 19px;
    color: var(--text-grey);
  }
</style>
</head>
<body>

  <section class="card card--front" aria-label="Business card front">
    <div class="band-rule band-rule--top"></div>
    <div class="band"></div>
    <div class="band-rule band-rule--bottom"></div>
    <div class="emblem"><span class="emblem-name">BrightPath</span></div>
    <div class="identity">
      <h1 class="company-name">BrightPath Chiropractic<br>&amp; Holistic Center</h1>
      <p class="person-name">Marlene Okafor LMT</p>
      <p class="contact-line contact-line--phone">555-214-0193</p>
      <p class="contact-line">4215 Elm Ridge Rd., Suite 310, Larkmoor, LK 77482</p>
    </div>
  </section>

  <section class="card card--back" aria-label="Business card back">
    <div class="band-rule band-rule--top"></div>
    <div class="band"></div>
    <div class="band-rule band-rule--bottom"></div>
    <div class="emblem"><span class="emblem-name">BrightPath</span></div>
    <h2 class="services-heading">Our Services</h2>
    <ul class="services-list">
      <li>restoration of health and vitality | spinal exam | health assessment</li>
      <li>dietary &amp; fitness programs | lymphatic &amp; therapeutic massage</li>
      <li>detox &amp; remineralize body wraps | far infrared sauna therapy</li>
    </ul>
  </section>

</body>
</html>
```